Velvet Lantern rebranding my business with a new business card

I have my new logo and now I need a refresher on my business cards. I really want something fun and fresh. I like black background or anything to make the color pop.
Logo
Name: Velvet Lantern
Contact Info as stated below:
Mira Pellow
555-013-4762
Logo
Name: Velvet Lantern
Mira Pellow
555-013-4762
fb.me/VelvetLanternbyMira
Instagram: @VelvetLanternbyMira

Industry/Entity Type

Business

Contact Information for Business Card

double-sided. Logo on one side. Contact info on the other.

Requirements
Must have
• Logo
• Name: Velvet Lantern
• Contact Info as stated below:
• Mira Pellow
• 555-013-4762
• fb.me/VelvetLanternbyMira
• fb.me/VelvetLanternbyMira

```html
<!DOCTYPE html>
<html lang="en">
<head>
<meta charset="utf-8">
<title>Velvet Lantern — Business Cards</title>
<link rel="stylesheet" href="https://fonts.googleapis.com/css2?family=Cherry+Swash:wght@400;700&family=Raleway:wght@300;400&display=swap">
<style>
  :root {
    --backdrop: #c9c9c9;
    --card: #2e2b2b;
    --teal: #3fbfa5;
    --teal-dark: #2a9a84;
    --ink-light: #f2f2f2;
    --ink-muted: #9a9a9a;
    --ring-grey: #bdbdbd;
    --cream: #f4f0e4;
    --white: #ffffff;
  }
  * { box-sizing: border-box; margin: 0; padding: 0; }
  html, body { width: 1200px; height: 973px; overflow: hidden; }
  body { background: var(--backdrop); position: relative; font-family: "Raleway", sans-serif; }

  .card {
    position: absolute;
    width: 589px;
    height: 341px;
    background: var(--card);
    border-radius: 30px;
    overflow: hidden;
    box-shadow: 0 4px 10px rgba(0,0,0,0.35);
  }
  .card--front { left: 8px; top: 143px; }
  .card--back-grey { left: 605px; top: 143px; }
  .card--back-white { left: 8px; top: 490px; }
  .card--back-teal { left: 605px; top: 490px; }

  /* Front: contact side */
  .drip-border {
    position: absolute; left: 0; top: 0; width: 100%; height: 70px;
    background: linear-gradient(180deg, var(--teal) 0%, var(--teal) 70%, var(--teal-dark) 100%);
  }
  .brand-name {
    position: absolute; left: 0; width: 100%; text-align: center;
    font-family: "Cherry Swash", serif; color: var(--teal);
    font-size: 38px; letter-spacing: 1px;
    top: 96px; padding-left: 8px;
  }
  .role {
    position: absolute; left: 0; width: 100%; text-align: center; padding-left: 8px;
    top: 141px; font-size: 16px; color: var(--ink-muted);
  }
  .person {
    position: absolute; left: 0; width: 100%; text-align: center; padding-left: 8px;
    color: var(--ink-light); font-size: 22px; font-weight: 300; line-height: 27px;
  }
  .person--name { top: 193px; }
  .person--phone { top: 220px; }
  .social {
    position: absolute; left: 213px; width: 166px; height: 18px;
    background: var(--teal); border-radius: 9px;
    display: flex; align-items: center; gap: 5px; padding-left: 3px;
    font-size: 10px; color: var(--card); white-space: nowrap;
  }
  .social--fb { top: 277px; }
  .social--ig { top: 304px; }
  .social__dot { width: 12px; height: 12px; border-radius: 50%; background: var(--card); flex: none; }

  /* Back: logo sides */
  .logo-ring {
    position: absolute; border-radius: 50%;
    display: flex; align-items: center; justify-content: center;
  }
  .logo-name {
    font-family: "Cherry Swash", serif; font-size: 34px; text-align: center; line-height: 1.1;
  }
  .card--back-grey .logo-ring {
    left: 125px; top: 6px; width: 334px; height: 334px;
    border: 2px solid var(--ring-grey);
  }
  .card--back-grey .logo-name { color: var(--ring-grey); }
  .card--back-white .logo-ring {
    left: 151px; top: 26px; width: 292px; height: 292px;
    background: var(--white); border: 2px solid var(--teal);
    box-shadow: 0 0 0 6px var(--white);
  }
  .card--back-white .logo-name { color: var(--card); }
  .card--back-teal .logo-ring {
    left: 114px; top: -8px; width: 356px; height: 356px;
    border: 4px solid var(--teal);
  }
  .card--back-teal .logo-name { color: var(--cream); }
</style>
</head>
<body>
  <section class="card card--front" aria-label="Business card front">
    <div class="drip-border" role="img" aria-label="Teal dripping icing border along the top edge"></div>
    <h1 class="brand-name">Velvet Lantern</h1>
    <p class="role">Owner/Creator</p>
    <p class="person person--name">Mira Pellow</p>
    <p class="person person--phone">555-013-4762</p>
    <p class="social social--fb"><span class="social__dot"></span>fb.me/VelvetLanternbyMira</p>
    <p class="social social--ig"><span class="social__dot"></span>@VelvetLanternbyMira</p>
  </section>

  <section class="card card--back-grey" aria-label="Business card back, grey logo">
    <div class="logo-ring"><span class="logo-name">Velvet<br>Lantern</span></div>
  </section>

  <section class="card card--back-white" aria-label="Business card back, logo on white disc">
    <div class="logo-ring"><span class="logo-name">Velvet<br>Lantern</span></div>
  </section>

  <section class="card card--back-teal" aria-label="Business card back, colour logo">
    <div class="logo-ring"><span class="logo-name">Velvet<br>Lantern</span></div>
  </section>
</body>
</html>
```